VORTEQ

It’s is a startup business. We design and build new products.

Target Market(s)

For my first two products, they are targeting the laundry market, hanger accessory, and new modern style clothes dryer. I also have a Pet Treat product at patent stage, and there are other products not yet started but will be more engineering based. Therefore from young adults to older population

Industry/Entity Type

Colours of website to match the logo (att)

Coding

Coded - Design and coding required

Number of Pages Required

1 page

Font styles to use
Other font styles liked:
• Some of the same font as the logo

Colors

Designer to choose colors to be used in the design.

Requirements
Must have
• An upbeat vibe - the logo looks great so inline with that !
Should not have
• anything old fashioned and old style fonts

```html
<!DOCTYPE html>
<html lang="en">
<head>
<meta charset="UTF-8">
<title>VORTEQ – Innovation & Technical Services</title>
<link href="https://fonts.googleapis.com/css2?family=Orbitron:wght@500;600&family=Mulish:wght@400;500;600&display=swap" rel="stylesheet">
<style>
:root{
  --dark:#3f3f41;
  --teal:#10918a;
  --teal-light:#4fc3bd;
  --light:#f1f2f2;
  --white:#ffffff;
  --text:#3a3a3a;
  --muted:#5a5a5a;
  --accent-soft-dark:#4a4a4d;
  --accent-soft-light:#e4e6e6;
}
*{margin:0;padding:0;box-sizing:border-box}
html,body{width:1200px;height:2817px;overflow:hidden}
body{position:relative;background:var(--white);font-family:'Mulish',sans-serif;color:var(--text)}
.abs{position:absolute}
.display{font-family:'Orbitron',sans-serif;font-weight:600;letter-spacing:1px;text-transform:uppercase}

/* header + hero */
.hero-bg{left:0;top:0;width:1200px;height:586px;background:var(--dark)}
.brand{color:var(--white);font-family:'Mulish',sans-serif;font-weight:600;font-size:26px;letter-spacing:4px;display:flex;align-items:center;gap:10px}
.brand .dot{width:14px;height:14px;border-radius:50%;background:var(--teal)}
.brand-top{left:112px;top:40px}
.nav{left:515px;top:51px;font-size:13px;font-weight:600;color:var(--white)}
.nav a{color:inherit;text-decoration:none;position:absolute;white-space:nowrap}
.nav a.active{color:var(--teal-light)}
.btn{display:inline-flex;align-items:center;justify-content:center;font-size:13px;font-weight:600;text-transform:uppercase;border-radius:3px;white-space:nowrap}
.btn-solid{background:var(--teal);color:var(--white)}
.btn-ghost{border:1px solid var(--teal);color:var(--white)}
.btn-card{border:1px solid var(--teal);color:var(--text);font-size:11.5px;width:100px;height:34px}
.hero-title{left:112px;top:186px;width:560px;color:var(--white);font-size:21px;line-height:41px}
.hero-title span{color:var(--teal)}
.hero-text{left:110px;top:288px;width:500px;color:var(--white);font-size:16.5px;line-height:34px}
.hero-photo{left:732px;top:117px;width:468px;height:555px;border-radius:80px 0 0 64px;background:linear-gradient(140deg,#9fd3ea 0%,#3fa3d8 45%,#0f6fb4 75%,#5cc6ec 100%)}
.texture-dark{background:var(--accent-soft-dark)}
.texture-light{background:var(--accent-soft-light)}

/* products */
.section-title{left:0;width:1200px;text-align:center;font-size:24px;color:var(--dark)}
.card{background:var(--white);border-radius:10px;box-shadow:0 0 8px rgba(0,0,0,.08)}
.card::before{content:"";position:absolute;right:0;top:0;width:52px;height:40px;border-top:2px solid var(--teal);border-right:2px solid var(--teal);border-top-right-radius:10px}
.card::after{content:"";position:absolute;left:0;bottom:0;width:52px;height:52px;border-bottom:2px solid var(--teal);border-left:2px solid var(--teal);border-bottom-left-radius:10px}
.product{top:746px;width:234px;height:361px;text-align:center}
.product .img{position:absolute;left:9px;top:8px;width:216px;height:174px;border-radius:10px}
.product h3{position:absolute;top:206px;width:100%;font-size:15px;font-weight:600;color:var(--teal)}
.product p{position:absolute;top:236px;left:20px;right:20px;font-size:14px;line-height:28px;color:var(--muted)}
.product .btn{position:absolute;left:67px;top:306px}
.arrow{width:34px;height:34px;border:1.5px solid var(--dark);border-radius:50%}

/* industries */
.ind-bg{left:0;top:1191px;width:1200px;height:678px;background:var(--light)}
.ind-panel{left:0;top:1249px;width:467px;height:557px;background:var(--dark);border-radius:0 90px 90px 0}
.ind-text{left:76px;top:1326px;width:236px;color:var(--white);font-size:13.5px;line-height:30px}
.industry{top:1335px;width:376px;height:386px}
.industry .icon{position:absolute;left:30px;top:44px}
.industry h3{position:absolute;left:30px;top:136px;font-size:19px;color:var(--teal)}
.industry p{position:absolute;left:30px;right:26px;top:177px;font-size:16px;line-height:34px;color:var(--text)}
.industry .go{position:absolute;right:0;bottom:0;width:56px;height:64px;background:var(--teal);border-radius:56px 0 10px 0}

/* testimonial */
.testi-photo{left:112px;top:1949px;width:977px;height:482px;border-radius:80px 10px 10px 60px;background:linear-gradient(120deg,#d7dde0 0%,#8aa3ad 35%,#3e5865 60%,#c9d3d8 100%)}
.testi-card{left:143px;top:1990px;width:381px;height:400px;background:var(--white);border-radius:20px;text-align:center}
.testi-card h2{margin-top:52px;font-size:19px;color:var(--teal)}
.testi-card p{margin:18px 18px 0;font-size:15.5px;line-height:34.5px}
.testi-card .who{margin-top:14px;font-size:17px;font-weight:600;color:var(--dark)}
.testi-card .who span{color:var(--teal)}
.pager{display:flex;justify-content:center;gap:13px;margin-top:30px}
.pager i{width:8px;height:8px;border-radius:50%;background:var(--teal)}

/* footer */
.footer{left:0;top:2517px;width:1200px;height:300px;background:var(--dark);color:var(--white)}
.brand-foot{left:0;width:1200px;top:2578px;justify-content:center;font-size:40px;letter-spacing:6px}
.rule{left:112px;width:977px;height:1px;background:#5a5a5c}
.contact{top:2683px;display:flex;align-items:center;gap:24px;font-size:14.5px;color:var(--white);white-space:nowrap}
.contact .ic{width:36px;height:36px;border-radius:50%;background:var(--teal);display:flex;align-items:center;justify-content:center}
.copy{left:0;width:1200px;top:2770px;text-align:center;font-size:12.5px;font-weight:600;color:var(--white)}
</style>
</head>
<body>

<div class="abs hero-bg"></div>
<div class="abs brand brand-top"><span class="dot"></span>VORTEQ</div>
<nav class="abs nav">
  <a class="active" style="left:0">HOME</a>
  <a style="left:65px">SERVICES</a>
  <a style="left:153px">PRODUCTS</a>
  <a style="left:250px">ABOUT</a>
  <a style="left:327px">CONTACT US</a>
</nav>
<a class="abs btn btn-solid" style="left:963px;top:40px;width:127px;height:38px">View Features</a>

<h1 class="abs display hero-title">Innovative <span>Products</span> for every generation.</h1>
<p class="abs hero-text">Lorem ipsum dolor sit amet, consectetur adipiscing elit, sed do eiusmod tempor incididunt ut labore et dolore magna aliqua enim ad minim veniam.</p>
<a class="abs btn btn-solid" style="left:110px;top:424px;width:142px;height:37px">Get Started Now</a>
<a class="abs btn btn-ghost" style="left:265px;top:424px;width:113px;height:37px">Contact Us</a>
<div class="abs texture-dark" role="img" aria-label="Decorative dot pattern" style="left:645px;top:302px;width:84px;height:190px"></div>
<div class="abs hero-photo" role="img" aria-label="Smiling woman at a laptop surrounded by glowing blue technology icons"></div>

<h2 class="abs display section-title" style="top:670px">Our Products</h2>
<div class="abs arrow" style="left:34px;top:823px">
  <svg width="31" height="31" viewBox="0 0 31 31"><path d="M18 9l-6 6.5 6 6.5" fill="none" stroke="#3f3f41" stroke-width="1.6"/></svg>
</div>
<div class="abs arrow" style="left:1120px;top:823px">
  <svg width="31" height="31" viewBox="0 0 31 31"><path d="M13 9l6 6.5-6 6.5" fill="none" stroke="#3f3f41" stroke-width="1.6"/></svg>
</div>

<div class="abs card product" style="left:112px">
  <div class="img" role="img" aria-label="Shirts on wooden hangers" style="background:linear-gradient(180deg,#e4e8ec,#9a9ea3)"></div>
  <h3>HANGERLOOP</h3><p>Lorem ipsum dolor sit amet, consectetur</p><a class="btn btn-card">View Details</a>
</div>
<div class="abs card product" style="left:358px">
  <div class="img" role="img" aria-label="Pile of pet treat pellets" style="background:linear-gradient(160deg,#a8561e,#6e3410)"></div>
  <h3>TREATNUGGET</h3><p>Lorem ipsum dolor sit amet, consectetur</p><a class="btn btn-card">View Details</a>
</div>
<div class="abs card product" style="left:605px">
  <div class="img" role="img" aria-label="Golden retriever wearing a collar in autumn leaves" style="background:linear-gradient(160deg,#b7a064,#d59a3f 60%,#8a6a2a)"></div>
  <h3>DOG COLLAR</h3><p>Lorem ipsum dolor sit amet, consectetur</p><a class="btn btn-card">View Details</a>
</div>
<div class="abs card product" style="left:851px">
  <div class="img" role="img" aria-label="Tabby cat playing with a toy" style="background:linear-gradient(160deg,#8c8070,#5d5246 55%,#d8d8d4)"></div>
  <h3>PET TOYS</h3><p>Lorem ipsum dolor sit amet, consectetur</p><a class="btn btn-card">View Details</a>
</div>

<div class="abs ind-bg"></div>
<div class="abs ind-panel"></div>
<div class="abs texture-light" role="img" aria-label="Decorative dot pattern" style="left:588px;top:1236px;width:86px;height:50px"></div>
<div class="abs texture-light" role="img" aria-label="Decorative dot pattern" style="left:1022px;top:1769px;width:86px;height:50px"></div>
<p class="abs ind-text">Lorem ipsum dolor sit amet, consectetur adipiscing elit, sed do eiusmod tempor incididunt ut labore et dolore magna aliqua. Ut enim ad minim veniam, quis nostrud exercitation ullamco laboris nisi ut aliquip ex ea commodo consequat. Duis aute irure dolor in reprehenderit in voluptate velit esse cillum dolore eu fugiat nulla pariatur. Excepteur sint occaecat cupidatat non proident, sunt in culpa qui officia deserunt mollit anim id est laborum.</p>

<div class="abs card industry" style="left:321px">
  <svg class="icon" width="58" height="58" viewBox="0 0 58 58" fill="none" stroke="#222" stroke-width="1.8">
    <rect x="10" y="3" width="45" height="52" rx="3"/><line x1="10" y1="15" x2="55" y2="15"/>
    <circle cx="34" cy="35" r="14"/><circle cx="34" cy="35" r="9"/>
    <circle cx="44" cy="9" r="1.5"/><circle cx="49" cy="9" r="1.5"/><line x1="3" y1="10" x2="3" y2="50"/>
  </svg>
  <h3 class="display">Laundry Industry</h3>
  <p>Lorem ipsum dolor sit amet, consectetur adipiscing elit, sed do eiusmod tempor incididunt ut labore et dolore magna aliqua enim ad minim veniam, quis nostrud exercitation ullamco laboris.</p>
  <span class="go"><svg width="56" height="64" viewBox="0 0 56 64"><path d="M28 26l7 8-7 8" fill="none" stroke="#fff" stroke-width="2.4"/></svg></span>
</div>
<div class="abs card industry" style="left:715px">
  <svg class="icon" width="58" height="58" viewBox="0 0 58 58" fill="none" stroke="#222" stroke-width="1.8">
    <circle cx="44" cy="12" r="7"/><path d="M14 24h26l4 6v10H14z"/>
    <line x1="18" y1="40" x2="14" y2="54"/><line x1="26" y1="40" x2="26" y2="54"/><line x1="36" y1="40" x2="36" y2="54"/><line x1="43" y1="40" x2="46" y2="54"/><path d="M14 26l-8-8"/>
  </svg>
  <h3 class="display">Pet Industry</h3>
  <p>Lorem ipsum dolor sit amet, consectetur adipiscing elit, sed do eiusmod tempor incididunt ut labore et dolore magna aliqua enim ad minim veniam, quis nostrud exercitation ullamco laboris.</p>
  <span class="go"><svg width="56" height="64" viewBox="0 0 56 64"><path d="M28 26l7 8-7 8" fill="none" stroke="#fff" stroke-width="2.4"/></svg></span>
</div>

<div class="abs texture-light" role="img" aria-label="Decorative dot pattern" style="left:72px;top:2285px;width:180px;height:192px;clip-path:polygon(0 0,20% 0,20% 78%,100% 78%,100% 100%,0 100%)"></div>
<div class="abs testi-photo" role="img" aria-label="Two engineers in hard hats reviewing a tablet in a factory"></div>
<div class="abs testi-card">
  <h2 class="display">Testimonials</h2>
  <p>"I've tried countless ways to organize my closet, but nothing has worked like this! The GripNest accessory keeps my clothes in place and wrinkle-free. My closet has never been so organized, and it's such a space saver. Highly recommend!"</p>
  <div class="who"><span>– MARA T.,</span> INTERIOR DESIGNER</div>
  <div class="pager"><i></i><i></i><i></i></div>
</div>

<div class="abs footer"></div>
<div class="abs brand brand-foot"><span class="dot" style="width:20px;height:20px"></span>VORTEQ</div>
<div class="abs rule" style="top:2658px"></div>
<div class="abs contact" style="left:112px">
  <span class="ic"><svg width="16" height="16" viewBox="0 0 24 24"><path d="M6.6 10.8a15 15 0 006.6 6.6l2.2-2.2a1 1 0 011-.25 11.4 11.4 0 003.6.57 1 1 0 011 1V20a1 1 0 01-1 1A17 17 0 013 4a1 1 0 011-1h3.5a1 1 0 011 1c0 1.25.2 2.45.57 3.57a1 1 0 01-.25 1z" fill="#fff"/></svg></span>+1 555 014 2210
</div>
<div class="abs contact" style="left:392px">
  <span class="ic"><svg width="16" height="16" viewBox="0 0 24 24"><rect x="3" y="5" width="18" height="14" rx="2" fill="#fff"/><path d="M3 6l9 7 9-7" fill="none" stroke="#10918a" stroke-width="1.8"/></svg></span>hello@vorteqstudio.com
</div>
<div class="abs contact" style="left:750px">
  <span class="ic"><svg width="16" height="16" viewBox="0 0 24 24"><path d="M12 2a7 7 0 00-7 7c0 5 7 13 7 13s7-8 7-13a7 7 0 00-7-7z" fill="#fff"/><circle cx="12" cy="9" r="2.6" fill="#10918a"/></svg></span>212 Vorteq Innovation &amp; Technical 640 115
</div>
<div class="abs rule" style="top:2737px"></div>
<div class="abs copy">©2025 COPYRIGHTS - ALL RIGHTS RESERVED</div>

</body>
</html>
```